Business Card Design Project

After recently finishing a design project for the company logo using markbazaar, it's now time for a business card. Attached to this is the logo.

The requirements for the business card are pretty straightforward:

- A clean, uncomplicated look
- Consistent usage of fonts
- Designs for both single sided and double sided cards
- A modern layout with preferably space to refer to social media accounts and/or downloadable vcards through a qr code
- consistent application of the company colour scheme: red/white. Hex codes for exact colour can be provided

Thanks!

```html
<!DOCTYPE html>
<html lang="en">
<head>
<meta charset="utf-8">
<title>Clayfield Recruiting – Business Cards</title>
<link rel="stylesheet" href="https://fonts.googleapis.com/css2?family=Source+Sans+3:ital,wght@0,400;0,600;0,700;1,700&display=swap">
<style>
  :root {
    --brand-red: #e31e2a;
    --ink: #231f20;
    --text: #333333;
    --card: #ffffff;
    --backdrop: #e9e6e2;
  }
  html, body {
    margin: 0;
    padding: 0;
    width: 960px;
    height: 1200px;
    overflow: hidden;
    background: var(--backdrop);
    font-family: "Source Sans 3", "Myriad Pro", sans-serif;
  }
  .canvas {
    position: relative;
    width: 960px;
    height: 1200px;
  }
  .card {
    position: absolute;
    width: 840px;
    height: 478px;
    background: var(--card);
    border-radius: 32px;
    overflow: hidden;
    box-shadow: 3px 4px 10px rgba(0,0,0,0.18);
  }
  .card--front { left: 58px; top: 82px; }
  .card--back  { left: 60px; top: 638px; height: 480px; }

  .wordmark {
    position: absolute;
    display: flex;
    align-items: center;
    gap: 26px;
  }
  .card--front .wordmark { left: 140px; top: 62px; }
  .card--back .wordmark  { left: 140px; top: 156px; }
  .wordmark__square {
    width: 92px;
    height: 92px;
    background: var(--brand-red);
    flex: none;
  }
  .wordmark__name {
    margin: 0;
    color: var(--ink);
    font-weight: 600;
    font-size: 64px;
    line-height: 0.98;
    letter-spacing: -0.5px;
  }

  .contact {
    position: absolute;
    left: 0;
    right: 0;
    top: 268px;
    text-align: center;
    color: var(--text);
  }
  .contact__person {
    margin: 0 0 20px;
    font-size: 21px;
  }
  .contact__name { font-weight: 700; font-size: 26px; }
  .contact__line {
    margin: 0 0 9px;
    font-size: 20px;
    line-height: 26px;
  }
  .contact__label { font-weight: 700; font-style: italic; }
  .contact__sep { margin: 0 8px; }

  .card__band {
    position: absolute;
    left: 0;
    bottom: 0;
    width: 840px;
    height: 80px;
    display: block;
  }
  .card__address {
    position: absolute;
    left: 0;
    right: 0;
    bottom: 12px;
    margin: 0;
    text-align: center;
    color: #ffffff;
    font-size: 22px;
  }
</style>
</head>
<body>
<div class="canvas">

  <section class="card card--front">
    <div class="wordmark">
      <span class="wordmark__square"></span>
      <h1 class="wordmark__name">Clayfield<br>Recruiting</h1>
    </div>

    <div class="contact">
      <p class="contact__person"><span class="contact__name">Your Name -</span> Designation</p>
      <p class="contact__line"><span class="contact__label">t</span> : 123-123-1234</p>
      <p class="contact__line"><span class="contact__label">e</span> : hello@clayfieldhire.com<span class="contact__sep">|</span><span class="contact__label">w</span> : www.clayfieldhire.com</p>
    </div>

    <svg class="card__band" viewBox="0 0 840 80" preserveAspectRatio="none" aria-hidden="true">
      <path d="M0 34 Q420 -18 840 34 L840 80 L0 80 Z" fill="var(--brand-red)"/>
      <path d="M0 24 Q420 -28 840 24" fill="none" stroke="var(--ink)" stroke-width="7"/>
    </svg>
    <p class="card__address">1234, Street Name, District, City, Country Code.</p>
  </section>

  <section class="card card--back">
    <div class="wordmark">
      <span class="wordmark__square"></span>
      <h2 class="wordmark__name">Clayfield<br>Recruiting</h2>
    </div>
  </section>

</div>
</body>
</html>
```